BRIGHT CORAL INC , CELL PHONE STORE

We need website design . we already have one but not happy with it www.brightcoralinc.example
we cell phones provide service ,phone repair ,
phone accessories.
online sale payment via PayVerra
shipping by QDMX

Industry/Entity Type

Cell Phone

Number of Pages Required

5+ page

Font styles to use
Serif
Sans Serif

Colors
3176b5

Requirements
Must have
• online sale via PayVerra
Nice to have
• email address

```html
<!DOCTYPE html>
<html lang="en">
<head>
<meta charset="utf-8">
<title>Bright Coral Inc – Cell Phone Store</title>
<link href="https://fonts.googleapis.com/css2?family=Open+Sans:wght@400;600;700&display=swap" rel="stylesheet">
<style>
:root{
  --brand:#3176b5;
  --brand-band:rgba(49,118,181,.92);
  --accent:#d9433b;
  --ink:#333;
  --muted:#777;
  --line:#d6d6d6;
  --soft:#f4f4f4;
  --topbar:#eeeeee;
  --white:#fff;
}
*{box-sizing:border-box;margin:0;padding:0}
html,body{width:720px;height:1200px;overflow:hidden;background:var(--white)}
body{font-family:"Open Sans",sans-serif;color:var(--ink);position:relative}
.abs{position:absolute}
svg{display:block}

.topbar{left:0;top:0;width:720px;height:24px;background:var(--topbar);font-size:8px;color:#666}
.topbar .item{position:absolute;top:7px;display:flex;align-items:center;gap:4px}

.header{left:0;top:24px;width:720px;height:58px;background:var(--white)}
.logo{left:80px;top:22px;font-size:14px;font-weight:600;color:var(--accent);letter-spacing:.3px}
.nav{right:80px;top:29px;display:flex;gap:19px;font-size:7.5px;color:#444}
.nav .active{color:var(--brand)}

.hero{left:0;top:82px;width:720px;height:287px}
.hero-photo{left:0;top:0;width:720px;height:238px;background:linear-gradient(120deg,#cfd3d6 0%,#eef0f1 40%,#3a3d42 55%,#e8eaec 70%,#b7c2cc 100%)}
.hero-band{left:0;top:238px;width:720px;height:49px;background:var(--brand-band);color:var(--white);font-weight:700;font-size:14px;text-align:center;line-height:49px;letter-spacing:.2px}
.hero-arrow{top:254px;width:17px;height:17px;border-radius:50%;background:rgba(255,255,255,.45)}

.service{top:382px;width:179px;height:53px;border:1px solid var(--line);display:flex;align-items:center;padding-left:34px;gap:12px}
.service .small{font-size:9.5px;color:#666;line-height:1.1}
.service .big{font-size:14px;color:#444;letter-spacing:.4px;line-height:1.2}

.showcase{left:0;top:449px;width:720px;height:288px;background:var(--soft)}
.tabs{left:0;top:35px;width:720px;display:flex;justify-content:center;gap:0;font-size:14px;font-weight:600;color:#999;letter-spacing:.3px}
.tabs span{padding:0 18px}
.tabs .sep{color:#ccc;padding:0;font-weight:400}
.tabs .current{color:var(--brand);position:relative}
.tab-underline{left:192px;top:55px;width:72px;height:2px;background:var(--brand)}
.tab-caret{left:222px;top:57px;width:0;height:0;border-left:6px solid transparent;border-right:6px solid transparent;border-top:6px solid var(--brand)}
.card{top:76px;width:131px;height:144px;background:var(--white)}
.card .shot{position:absolute;left:40px;top:20px;width:51px;height:104px;border-radius:8px;background:linear-gradient(160deg,#8fd0ff,#f3b6e6 60%,#cfd5da)}
.card .caption{position:absolute;top:151px;left:0;width:131px;text-align:center;font-size:7.5px;color:var(--brand)}
.card .price{position:absolute;top:163px;left:0;width:131px;text-align:center;font-size:7px;color:#333}
.card .btn{position:absolute;top:126px;width:19px;height:18px;background:#7fa9d1}

.brands-title{left:0;top:782px;width:720px;text-align:center;font-size:9.5px;letter-spacing:.5px;color:#444}
.brand{top:812px;font-size:11px;font-weight:600;color:#555}

.promo{top:878px;height:72px}
.promo .fill{position:absolute;inset:0}
.promo .title{position:absolute;font-size:9.5px;font-weight:600;color:var(--brand);letter-spacing:.3px}
.promo .sub{position:absolute;font-size:8.5px;color:#333}
.pay{position:absolute;top:42px;height:13px;padding:0 3px;background:var(--white);border:1px solid #ccc;font-size:5.5px;font-weight:600;color:#444;line-height:11px}

.footer{left:0;top:998px;width:720px;height:155px;background:var(--soft)}
.fcol{top:40px;font-size:8.5px;color:#333}
.fcol h4{font-weight:400;font-size:8.5px;margin-bottom:9px}
.fcol ul{list-style:none;font-size:6px;color:#666}
.fcol li{margin-bottom:8px}
.fcol li::before{content:"•";margin-right:4px}
.contact-row{display:flex;gap:9px;align-items:center;font-size:7px;color:#444;margin-bottom:10px}
.social{display:flex;align-items:center;gap:4px;font-size:6.5px;color:#444;margin-bottom:7px}
.social i{width:10px;height:10px;border-radius:50%;display:block}
.copybar{left:0;top:1153px;width:720px;height:47px;background:var(--soft);border-top:1px solid #e2e2e2;text-align:center;font-size:7px;color:#555;line-height:47px}
</style>
</head>
<body>

<div class="abs topbar">
  <div class="item" style="left:80px"><svg width="5" height="7" viewBox="0 0 5 7"><rect x=".5" y=".5" width="4" height="6" rx=".6" fill="none" stroke="#666"/></svg>1 555 014 2290</div>
  <div class="item" style="left:167px"><svg width="7" height="5" viewBox="0 0 7 5"><rect width="7" height="5" fill="#666"/><path d="M0 0l3.5 2.6L7 0" stroke="#eee" fill="none" stroke-width=".7"/></svg>brightcoralinc@mail.example</div>
  <div class="item" style="left:312px"><svg width="6" height="6" viewBox="0 0 6 6"><path d="M1 5l1-1 3-3 .7.7-3 3-1 1z" fill="#666"/></svg>Register</div>
  <div class="item" style="left:393px"><svg width="5" height="7" viewBox="0 0 5 7"><path d="M1 3V2a1.5 1.5 0 013 0v1" stroke="#666" fill="none"/><rect y="3" width="5" height="4" fill="#666"/></svg>Login</div>
  <div class="item" style="left:460px"><svg width="7" height="6" viewBox="0 0 7 6"><path d="M3.5 6L.5 3A1.6 1.6 0 013.5 1a1.6 1.6 0 013 2z" fill="#666"/></svg>Wishlist</div>
  <div class="item" style="left:538px"><svg width="7" height="6" viewBox="0 0 7 6"><path d="M0 0h1.2l.8 3.5h4L7 1H2" fill="#666"/><circle cx="2.5" cy="5.3" r=".6" fill="#666"/><circle cx="5.5" cy="5.3" r=".6" fill="#666"/></svg>My Cart - 0 items - $00.00</div>
</div>

<header class="abs header">
  <div class="abs logo">BRIGHT CORAL INC</div>
  <nav class="abs nav">
    <span class="active">Home</span><span>About Us</span><span>Phone Repair</span><span>Mobiles</span><span>Products</span><span>Bill Payment</span><span>Contact Us</span>
  </nav>
</header>

<section class="abs hero">
  <div class="abs hero-photo" role="img" aria-label="Technician in gloves repairing an opened smartphone on a workbench with tools"></div>
  <div class="abs hero-band">WE CAN COME TO YOU - FIX YOUR PHONE IN YOUR HOME OR YOUR WORK!</div>
  <div class="abs hero-arrow" style="left:15px"><svg width="17" height="17" viewBox="0 0 17 17"><path d="M10 5L6.5 8.5 10 12" stroke="#fff" stroke-width="2" fill="none"/></svg></div>
  <div class="abs hero-arrow" style="left:688px"><svg width="17" height="17" viewBox="0 0 17 17"><path d="M7 5l3.5 3.5L7 12" stroke="#fff" stroke-width="2" fill="none"/></svg></div>
</section>

<div class="abs service" style="left:80px">
  <svg width="13" height="22" viewBox="0 0 13 22"><rect x=".5" y=".5" width="12" height="21" rx="1.5" fill="none" stroke="#777"/><line x1="3" y1="3" x2="10" y2="3" stroke="#777"/><line x1="1" y1="17.5" x2="12" y2="17.5" stroke="#777"/></svg>
  <div><div class="small">Cell Phone</div><div class="big">SERVICES</div></div>
</div>
<div class="abs service" style="left:270px;padding-left:26px">
  <svg width="22" height="22" viewBox="0 0 22 22" fill="none" stroke="#777"><path d="M3 19L15 7M5 3a4 4 0 015 5l-1 1M19 3L7 15M17 19a4 4 0 01-5-5"/><circle cx="4" cy="4" r="2"/><circle cx="18" cy="18" r="2"/></svg>
  <div><div class="small">Cell Phone</div><div class="big">REPAIRS</div></div>
</div>
<div class="abs service" style="left:461px;padding-left:26px">
  <svg width="24" height="18" viewBox="0 0 24 18" fill="none" stroke="#777"><path d="M1 7l11-6 11 6-11 6z"/><path d="M1 11l11 6 11-6"/></svg>
  <div><div class="small">Cell Phone</div><div class="big">ACCESSORIES</div></div>
</div>

<section class="abs showcase">
  <div class="abs tabs"><span class="current">FEATURED</span><span class="sep">|</span><span>NEW ARRIVALS</span><span class="sep">|</span><span>BEST SELLER</span></div>
  <div class="abs tab-underline"></div>
  <div class="abs tab-caret"></div>

  <div class="abs card" style="left:80px">
    <div class="shot" role="img" aria-label="White smartphone with colourful curved wallpaper"></div>
    <div class="btn" style="left:0"><svg width="19" height="18" viewBox="0 0 19 18"><path d="M9.5 13L6 9.5A2 2 0 019.5 7a2 2 0 013.5 2.5z" fill="none" stroke="#fff"/></svg></div>
    <div class="btn" style="left:112px"><svg width="19" height="18" viewBox="0 0 19 18"><path d="M5 6h1.3l1 4h4.5L13 7.2H7" fill="#fff"/><circle cx="8" cy="11.5" r=".7" fill="#fff"/><circle cx="11.5" cy="11.5" r=".7" fill="#fff"/></svg></div>
    <div class="caption">Duis pellentesque</div><div class="price">$00.00</div>
  </div>
  <div class="abs card" style="left:222px">
    <div class="shot" role="img" aria-label="Dark smartphone with multicoloured geometric wallpaper" style="background:linear-gradient(150deg,#2b2d33 8%,#f2c14b 30%,#e24a7a 50%,#3b8fe0 70%,#2b2d33 92%)"></div>
    <div class="caption">Duis pellentesque</div><div class="price">$00.00</div>
  </div>
  <div class="abs card" style="left:366px">
    <div class="shot" role="img" aria-label="Black smartphone with night sky wallpaper" style="background:linear-gradient(180deg,#1b1c20 8%,#4a4a6a 40%,#8a6f8f 70%,#1b1c20 92%)"></div>
    <div class="caption">Duis pellentesque</div><div class="price">$00.00</div>
  </div>
  <div class="abs card" style="left:510px">
    <div class="shot" role="img" aria-label="White smartphone with meadow and balloons wallpaper" style="background:linear-gradient(180deg,#e9ecef 6%,#5fa8e8 25%,#f0b23a 50%,#5ab24a 75%,#e9ecef 94%)"></div>
    <div class="caption">Duis pellentesque</div><div class="price">$00.00</div>
  </div>
</section>

<div class="abs brands-title">TOP BRANDS</div>
<div class="abs brand" style="left:82px">Tellon</div>
<div class="abs brand" style="left:198px">Ultrix</div>
<div class="abs brand" style="left:300px">NetWave</div>
<div class="abs brand" style="left:400px">Sonaro</div>
<div class="abs brand" style="left:508px">Pomme</div>
<div class="abs brand" style="left:606px">Bolto</div>

<div class="abs promo" style="left:80px;width:280px">
  <div class="fill" role="img" aria-label="Hand holding a smartphone for fast delivery" style="background:linear-gradient(90deg,#f7f6ef 0%,#f1ead8 45%,#d9a88a 70%,#2c2f3a 85%,#e8c0a4 100%)"></div>
  <div class="title" style="left:14px;top:22px">FAST DELIVERY</div>
  <div class="sub" style="left:14px;top:37px">We Deliver All Manhattan</div>
</div>
<div class="abs promo" style="left:360px;width:280px">
  <div class="fill" role="img" aria-label="Hands typing card details on a laptop keyboard" style="background:linear-gradient(90deg,#f8f8f8 0%,#f4f4f4 50%,#d8dde3 70%,#efd2bf 85%,#f6f6f6 100%)"></div>
  <div class="title" style="left:18px;top:21px">SECURE PAYMENTS</div>
  <span class="pay" style="left:18px">QDMX</span>
  <span class="pay" style="left:47px">PayVerra</span>
  <span class="pay" style="left:86px">Findr</span>
  <span class="pay" style="left:115px">Vexa E</span>
  <span class="pay" style="left:148px">Vexa</span>
</div>

<footer class="abs footer">
  <div class="abs fcol" style="left:80px;width:190px">
    <p style="line-height:1.45;margin-bottom:14px">Feel Free To Contact Us Via Phone,Email Or Just Send Us Mail.</p>
    <div class="contact-row"><svg width="5" height="7" viewBox="0 0 5 7"><path d="M2.5 7S0 3.8 0 2.5a2.5 2.5 0 015 0C5 3.8 2.5 7 2.5 7z" fill="#444"/></svg>48 Harbor Lane, LAKEVIEW, NY 10500.</div>
    <div class="contact-row"><svg width="5" height="7" viewBox="0 0 5 7"><rect x=".5" y=".5" width="4" height="6" rx=".6" fill="none" stroke="#444"/></svg>1 555 014 2290</div>
    <div class="contact-row"><svg width="7" height="5" viewBox="0 0 7 5"><rect width="7" height="5" fill="#444"/><path d="M0 0l3.5 2.6L7 0" stroke="#f4f4f4" fill="none" stroke-width=".7"/></svg>BRIGHTCORALINC@MAIL.EXAMPLE</div>
  </div>
  <div class="abs fcol" style="left:287px"><h4>Customer Service</h4><ul><li>Contact Us</li><li>Privacy Policy</li><li>Terms &amp; Conditions</li></ul></div>
  <div class="abs fcol" style="left:398px"><h4>Quick Links</h4><ul><li>Login</li><li>New Customers</li><li>Products</li><li>Phone Repair</li></ul></div>
  <div class="abs fcol" style="left:493px"><h4>Information</h4><ul><li>Home</li><li>About Us</li></ul></div>
  <div class="abs fcol" style="left:591px">
    <h4>Share us on</h4>
    <div class="social"><i style="background:#3b5998"></i>Friendly</div>
    <div class="social"><i style="background:#2aa3ef"></i>Chirp</div>
    <div class="social"><i style="background:#d0392f"></i>Rated</div>
  </div>
</footer>
<div class="abs copybar">Copyright © 2017 Company name. All rights reserved.</div>

</body>
</html>
```